8'x8' Exhibit Backdrop for Healthcare Events focused on the 55 and older crowds

8X8 Backdrop for Exhibiting.

I also want a design for a 6' table skirt to include our logo on two sides and the logo with Hereditary Cancer Screening underneath on the front. I want the main message of Will You Give your Loved Ones The Information To Beat Cancer in Their Lives to be completely centered on the 8X8 backdrop. Hereditary Cancer Screening The Test You Take For Them in the top left corner and the purple box on the right hand side - just like the photo that has been uploaded below. I need High resolution photos around the backdrop but not so large that they overtake the main message.

Target Market(s)

55+ crowd living in Adult only communities. They have an active lifestyle

Industry/Entity Type

Healthcare

Other font styles liked:
• "The Test You Take For Them" is Comic Sans

Colors
0255a3
fbed22
ffffff

Requirements
Must have
• I am posting a photo of the exact backdrop I would like to see. There are red arrows showing where to move certain items. There is a space underneath the slogan WILL YOU GIVE YOUR LOVED ONES... where another photo will go. Add another photo underneath the slogan that you are moving up - GIVE THEM THE GIFT OF KNOWLEDGE
• See the upload section for the new photo
• Do this one exactly like I am asking for and then you can show me some of your ideas. Thanks
• THE PHOTOS UPLOADED ARE EXAMPLES. FEEL FREE TO SEARCH OUT YOUR OWN HIGH RESOLUTION PHOTOS. THANKS

```html
<!DOCTYPE html>
<html lang="en">
<head>
<meta charset="utf-8">
<title>Hereditary Cancer Screening Backdrop</title>
<link rel="stylesheet" href="https://fonts.googleapis.com/css2?family=Oswald:wght@500;600&family=Roboto:wght@500;700&family=Comic+Neue:wght@400&display=swap">
<style>
  :root {
    --navy: #0b1d5c;
    --green: #7cc242;
    --white: #ffffff;
    --page: #eeeeee;
  }
  * { box-sizing: border-box; margin: 0; padding: 0; }
  html, body { width: 1200px; height: 977px; overflow: hidden; background: var(--page); }
  .backdrop {
    position: absolute; left: 96px; top: 3px; width: 1008px; height: 970px;
    background: var(--navy); border-radius: 14px 14px 0 0; overflow: hidden;
    font-family: "Roboto", Arial, sans-serif;
  }
  .headline {
    position: absolute; left: 40px; top: 38px; width: 312px; text-align: right;
    color: var(--white); font-size: 50px; line-height: 54px; font-weight: 500;
  }
  .headline strong { font-weight: 700; }
  .tagline {
    position: absolute; left: 78px; top: 214px; width: 274px; height: 36px;
    background: var(--green); color: var(--white);
    font-family: "Comic Neue", "Comic Sans MS", cursive; font-size: 18px;
    display: flex; align-items: center; justify-content: center;
  }
  .photo {
    position: absolute; border: 2px solid var(--white); border-radius: 14px; overflow: hidden;
  }
  .photo-1 { left: 366px; top: 46px; width: 276px; height: 206px; background: linear-gradient(135deg, #e9ddc9, #8a6a55); }
  .photo-2 { left: 656px; top: 46px; width: 276px; height: 206px; background: linear-gradient(135deg, #cbb9a3, #6d4c3d); }
  .photo-3 { left: 76px; top: 264px; width: 276px; height: 228px; background: linear-gradient(135deg, #7fa26a, #5f6a74); }
  .photo-4 { left: 76px; top: 506px; width: 276px; height: 228px; background: linear-gradient(135deg, #8fb579, #e9e4dc 60%, #4d8fc4); }
  .photo-5 { left: 366px; top: 506px; width: 276px; height: 228px; background: linear-gradient(135deg, #f4f2ee, #d9c0ac 60%, #2d4f8a); }
  .photo-6 {
    left: 656px; top: 264px; width: 276px; height: 470px;
    background: linear-gradient(180deg, #3a4a6e 0%, #6b7d83 35%, #7d9a72 58%, var(--green) 78%, var(--green) 100%);
  }
  .gift {
    position: absolute; right: 22px; bottom: 22px; text-align: right;
    font-family: "Oswald", "Arial Narrow", sans-serif; font-weight: 500;
    color: var(--white); font-size: 36px; line-height: 46px;
  }
  .gift .accent { color: var(--navy); font-size: 56px; font-weight: 600; }
  .message {
    position: absolute; left: 366px; top: 264px; width: 276px; height: 228px;
    display: flex; flex-direction: column; justify-content: center; align-items: center;
    text-align: center; white-space: nowrap;
    font-family: "Oswald", "Arial Narrow", sans-serif; font-weight: 500;
    color: var(--white);
  }
  .message .line { display: block; font-size: 26px; line-height: 31px; }
  .message .line-small { font-size: 22px; line-height: 27px; }
  .message .give { color: var(--green); font-size: 40px; font-weight: 600; line-height: 44px; }
  .message .cancer { color: var(--green); font-size: 64px; font-weight: 600; line-height: 66px; }
  .footer { position: absolute; left: 0; top: 740px; width: 1008px; height: 230px; }
  .brand {
    position: absolute; left: 80px; top: 835px; display: flex; align-items: center; gap: 18px;
  }
  .brand-mark { width: 96px; height: 96px; border-radius: 50%; background: var(--navy); }
  .brand-name {
    color: var(--navy); font-weight: 700; font-size: 34px; line-height: 36px; letter-spacing: 1px;
  }
  .website {
    position: absolute; right: 78px; top: 906px; color: var(--navy);
    font-weight: 700; font-size: 28px;
  }
</style>
</head>
<body>
  <div class="backdrop">
    <h1 class="headline"><strong>Hereditary</strong><br>Cancer<br>Screening</h1>
    <div class="tagline">The Test You Take For Them</div>

    <div class="photo photo-1" role="img" aria-label="Grandfather hugging his granddaughter"></div>
    <div class="photo photo-2" role="img" aria-label="Grandmother embracing her granddaughter"></div>
    <div class="photo photo-3" role="img" aria-label="Young boy leaning on his grandfather outdoors"></div>
    <div class="photo photo-4" role="img" aria-label="Smiling grandfather with his grandson in a garden"></div>
    <div class="photo photo-5" role="img" aria-label="Laughing grandmother cheek to cheek with a little girl"></div>
    <div class="photo photo-6" role="img" aria-label="Father hugging his laughing young son on steps">
      <div class="gift">GIVE THEM<br>THE <span class="accent">GIFT</span><br>OF KNOWLEDGE</div>
    </div>

    <p class="message">
      <span class="line">WILL YOU <span class="give">GIVE</span></span>
      <span class="line">YOUR LOVED ONES</span>
      <span class="line line-small">THE INFORMATION TO BEAT</span>
      <span class="line cancer">CANCER</span>
      <span class="line">IN THEIR LIVES?</span>
    </p>

    <svg class="footer" width="1008" height="230" viewBox="0 0 1008 230">
      <path d="M0 30 C 200 -10, 420 10, 620 60 C 780 100, 900 95, 1008 70 L1008 230 L0 230 Z" fill="#7cc242"/>
      <path d="M0 48 C 200 14, 420 34, 620 82 C 780 120, 900 116, 1008 92 L1008 230 L0 230 Z" fill="#ffffff"/>
    </svg>

    <div class="brand">
      <div class="brand-mark"></div>
      <div class="brand-name">KINFOLK<br>HEALTH<br>GROUP</div>
    </div>
    <div class="website">www.kinfolkhealthgroup.com</div>
  </div>
</body>
</html>
```